Logo and Simple Website - Lumo IT

I require a good logo and simple website for an IT trading business. I am uploading the website text and description.
For the logo, I was thinking of something that has a (partial) cube but also looks a bit like a circuit board. The name should be easy to read, but there should also be a graphical element to the logo. The graphical element can be used on its own for tabs or headers on the website. The logo needs to be suitable for business cards and stationery as well.
I am open to color schemes, but perhaps something in purple tones.

Target Market(s)

Corporate clients

Industry/Entity Type

It Professional

Logo Text

Lumo IT

Number of Pages Required

1 page

Font styles to use
Other font styles liked:
• Eurostyle, Futura

Colors

Designer to choose colors to be used in the design.

Requirements
Must have
• Simple, streamlined look, but should not look too basic.

```html
<!DOCTYPE html>
<html lang="en">
<head>
<meta charset="utf-8">
<title>Lumo IT</title>
<link rel="stylesheet" href="https://fonts.googleapis.com/css2?family=Jost:wght@400;500&family=Open+Sans:wght@400;600&display=swap">
<style>
:root{
  --purple:#7b1070;
  --purple-dark:#5a0b55;
  --purple-head:#8a1a7e;
  --grey-band:#efefef;
  --box:#eeeeee;
  --text:#444;
  --white:#fff;
  --line:#c9c9c9;
}
*{box-sizing:border-box;margin:0;padding:0}
html,body{width:1200px;height:4000px;overflow:hidden}
body{position:relative;background:var(--white);font-family:"Open Sans",Arial,sans-serif;color:var(--text)}
.abs{position:absolute}
h2{font-family:"Jost",Arial,sans-serif;font-weight:400;color:var(--purple-head)}

/* header */
.site-header{left:0;top:0;width:1200px;height:105px;background:var(--white)}
.brand{left:145px;top:24px;display:flex;align-items:center;gap:14px}
.brand-mark{width:52px;height:52px;background:var(--purple);border-radius:4px}
.brand-name{font-family:"Jost",sans-serif;font-size:46px;font-weight:500;color:#3a3a3a}
.main-nav{right:145px;top:40px;display:flex;gap:44px;font-size:15px;font-family:"Open Sans",sans-serif}
.main-nav a{color:#444;text-decoration:none}
.main-nav a.active{color:var(--purple)}

/* hero */
.hero{left:0;top:105px;width:1200px;height:645px;clip-path:polygon(0 0,100% 0,100% 510px,50% 100%,0 510px);
  background:linear-gradient(135deg,#3d0840 0%,#8b1a86 45%,#5e0f63 70%,#b02aa8 100%)}
.hero-title{left:0;top:180px;width:1200px;text-align:center;font-family:"Jost",sans-serif;font-size:44px;line-height:50px;color:var(--white)}
.hero-btn{left:544px;top:305px;width:112px;height:40px;background:var(--white);color:var(--purple);font-size:14px;line-height:40px;text-align:center}
.hero-arrow{top:240px;width:20px;height:30px}
.hero-dots{left:540px;top:560px;display:flex;gap:10px}
.hero-dots span{width:14px;height:4px;background:rgba(255,255,255,.5)}
.hero-dots span.on{background:var(--white)}

/* about */
.about h2{font-size:36px}
.about-title{left:145px;top:820px}
.about-text{left:145px;top:882px;width:545px;font-size:13.5px;line-height:24px}
.about-text p{margin-bottom:24px}
.about-photo{left:730px;top:825px;width:325px;height:410px;clip-path:polygon(50% 0,100% 25%,100% 75%,50% 100%,0 75%,0 25%);
  background:linear-gradient(160deg,#dfe6ee,#8f9aa8 55%,#3f4a58)}

/* team */
.team-band{left:0;top:1385px;width:1200px;height:588px;background:var(--grey-band);clip-path:polygon(0 55px,50% 0,100% 55px,100% 100%,0 100%)}
.section-title{left:0;width:1200px;text-align:center;font-size:36px}
.section-lead{left:150px;width:900px;text-align:center;font-size:16.5px;line-height:28px}
.member{top:1630px;width:240px;text-align:center}
.member-photo{width:240px;height:210px;position:relative}
.member-photo .diamond{position:absolute;left:46px;top:31px;width:148px;height:148px;transform:rotate(45deg);background:#c4c4c4}
.member-photo .portrait{position:absolute;left:60px;top:0;width:120px;height:210px;background:linear-gradient(180deg,#d9cfc6,#8a8683 60%,#2f3238)}
.member-name{margin-top:10px;font-family:"Jost",sans-serif;font-size:21px;color:var(--purple-head)}
.member-role{font-size:13px;color:#333;margin-top:2px}
.team-arrow{top:1720px;width:16px;height:26px}

/* products */
.brand-box{top:2176px;width:437px;height:309px;background:var(--box)}
.box-title{position:absolute;left:0;top:26px;width:100%;text-align:center;font-family:"Jost",sans-serif;font-size:20px;color:var(--purple-head)}
.brand-grid{position:absolute;left:30px;top:80px;width:377px;display:grid;grid-template-columns:1fr 1fr;row-gap:34px;text-align:center}
.brand-grid span{font-family:"Jost",sans-serif;font-weight:500;font-size:22px;color:#222;height:36px;line-height:36px}
.brand-grid .solo{grid-column:1/3}

/* services */
.services-band{left:0;top:2565px;width:1200px;height:656px;background:linear-gradient(180deg,#6e0e67,#5a0b55);clip-path:polygon(0 0,100% 0,100% 528px,50% 100%,0 528px)}
.services-photo{left:147px;top:2653px;width:320px;height:400px;clip-path:polygon(50% 0,100% 25%,100% 75%,50% 100%,0 75%,0 25%);
  background:radial-gradient(circle at 55% 50%,#f4b8f0,#c23cc0 45%,#5a0f70 90%)}
.services-title{left:515px;top:2730px;font-size:36px;color:var(--white)}
.services-text{left:515px;top:2790px;width:540px;font-size:13px;line-height:24px;color:#f3dff0}
.services-text p{margin-bottom:24px}

/* contact */
.field{height:36px;border:1px solid var(--line);font-size:12px;color:#777;padding:10px 14px;background:var(--white)}
.submit{left:544px;top:3565px;width:112px;height:38px;background:var(--purple);color:var(--white);font-size:14px;font-weight:600;line-height:38px;text-align:center}

/* footer */
.footer-band{left:0;top:3685px;width:1200px;height:315px;background:var(--purple);clip-path:polygon(0 128px,50% 0,100% 128px,100% 100%,0 100%)}
.footer-address{left:0;top:3780px;width:1200px;text-align:center;font-family:"Jost",sans-serif;font-size:17px;color:var(--white)}
.footer-contacts{left:0;top:3818px;width:1200px;text-align:center;font-family:"Jost",sans-serif;font-size:23px;color:var(--white);display:flex;justify-content:center;align-items:center;gap:16px}
.footer-rule{left:145px;top:3882px;width:910px;height:1px;background:rgba(255,255,255,.35)}
.footer-nav{left:145px;top:3908px;font-size:12px;color:var(--white)}
.footer-copy{left:145px;top:3944px;font-size:12px;color:#e9cfe6}
.social{top:3924px;width:18px;height:18px;border-radius:50%;background:rgba(255,255,255,.75)}
</style>
</head>
<body>

<header class="site-header abs">
  <div class="brand abs"><span class="brand-mark"></span><span class="brand-name">Lumo IT</span></div>
  <nav class="main-nav abs">
    <a class="active" href="#">HOME</a><a href="#">ABOUT US</a><a href="#">OUR TEAM</a><a href="#">PRODUCTS</a><a href="#">SERVICES</a><a href="#">CONTACT</a>
  </nav>
</header>

<section class="hero abs" role="img" aria-label="Server room racks lit in purple">
  <div class="hero-title abs">Maecenas vel tortor accumsan<br>quam varius imperdiet</div>
  <div class="hero-btn abs">READ MORE</div>
  <svg class="hero-arrow abs" style="left:52px" viewBox="0 0 20 30"><path d="M15 3 4 15l11 12" fill="none" stroke="#fff" stroke-width="3"/></svg>
  <svg class="hero-arrow abs" style="left:1128px" viewBox="0 0 20 30"><path d="M5 3l11 12L5 27" fill="none" stroke="#fff" stroke-width="3"/></svg>
  <div class="hero-dots abs"><span class="on"></span><span></span><span></span><span></span></div>
</section>

<section class="about">
  <h2 class="about-title abs">About Us</h2>
  <div class="about-text abs">
    <p>We are a specialized IT trading company, with a focus on high end storage solutions. As businesses and individuals continue to generate ever-greater amounts of data, storage technologies need to keep pace. We believe that understanding the needs of our customers puts us in an excellent position to fulfill their requirements in this fast evolving market.</p>
    <p>We operate in the Middle East, Africa and the CIS, and are particularly well suited to the complex dynamics of these markets. We understand the need for cost consciousness and are motivated by a desire to provide first-rate products and professional services to a wide customer base.</p>
    <p>From our logistics hub, we are able to provide cost effective and speedy transportation to our customers. We are motivated by the desire to build real partnerships with our customers, and always aim to provide solutions that guarantee profitability for all participants in the value chain.</p>
  </div>
  <div class="about-photo abs" role="img" aria-label="Technician installing a server drive"></div>
</section>

<section class="team">
  <div class="team-band abs"></div>
  <h2 class="section-title abs" style="top:1440px">Our Team</h2>
  <p class="section-lead abs" style="top:1492px">Our team is here to serve you. All of our sales professionals and technical support staff have a passion for information technology, and are dedicated to our customers.</p>
  <p class="section-lead abs" style="top:1568px">Our management team comprises individuals with many years of in-depth experience in the storage solutions sector.</p>
  <svg class="team-arrow abs" style="left:53px" viewBox="0 0 16 26"><path d="M13 2 3 13l10 11" fill="none" stroke="#777" stroke-width="2.5"/></svg>
  <svg class="team-arrow abs" style="left:1131px" viewBox="0 0 16 26"><path d="M3 2l10 11L3 24" fill="none" stroke="#777" stroke-width="2.5"/></svg>
  <div class="member abs" style="left:173px">
    <div class="member-photo"><div class="diamond"></div><div class="portrait" role="img" aria-label="Portrait of team member Marcus Hale"></div></div>
    <div class="member-name">Marcus Hale</div><div class="member-role">Aliquam erat volutpat</div>
  </div>
  <div class="member abs" style="left:480px">
    <div class="member-photo"><div class="diamond"></div><div class="portrait" role="img" aria-label="Portrait of team member Nadia"></div></div>
    <div class="member-name">Nadia</div><div class="member-role">Duis hendrerit arcu</div>
  </div>
  <div class="member abs" style="left:787px">
    <div class="member-photo"><div class="diamond"></div><div class="portrait" role="img" aria-label="Portrait of team member Oliver"></div></div>
    <div class="member-name">Oliver</div><div class="member-role">Pellentesque vehicula</div>
  </div>
</section>

<section class="products">
  <h2 class="section-title abs" style="top:2042px">Products</h2>
  <p class="section-lead abs" style="top:2092px;left:120px;width:960px">As a high end storage specialist, we trade in memory, as well as Hard Disk Drives and Solid State Drives. Whether it be mass market product ranges, or specialized products, we will be able to source and deliver at the most competitive price.</p>
  <div class="brand-box abs" style="left:147px">
    <div class="box-title">Memory</div>
    <div class="brand-grid"><span>Vantor</span><span>Corevia</span><span>Bitfield</span><span>Kestrel</span><span class="solo">Novamem</span></div>
  </div>
  <div class="brand-box abs" style="left:616px">
    <div class="box-title">Storage</div>
    <div class="brand-grid"><span>Ridgeway Data</span><span>Tidewell</span><span>Harumi</span><span>Quarra</span><span>Tosuna</span><span>Fenrix</span></div>
  </div>
</section>

<section class="services">
  <div class="services-band abs" role="img" aria-label="Purple circuit board texture"></div>
  <div class="services-photo abs" role="img" aria-label="Open hard disk drive platter in purple light"></div>
  <h2 class="services-title abs">Services</h2>
  <div class="services-text abs">
    <p>We are first and foremost a trusted supplier of storage products. In this respect, our strong technical expertise and wide range of experience allows us to consult clients on the best strategy for meeting their data storage needs, coupled with a clear commitment for delivering the products required to execute this.</p>
    <p>We work with blanket orders as required, giving customers the possibility to secure stock and plan ahead without the worry of product shortages or price fluctuations.</p>
  </div>
</section>

<section class="contact">
  <h2 class="section-title abs" style="top:3296px">Contact</h2>
  <div class="field abs" style="left:147px;top:3360px;width:216px">Name</div>
  <div class="field abs" style="left:376px;top:3360px;width:216px">Company Name</div>
  <div class="field abs" style="left:608px;top:3360px;width:216px">Email</div>
  <div class="field abs" style="left:837px;top:3360px;width:216px">Phone</div>
  <div class="field abs" style="left:147px;top:3416px;width:906px;height:126px">Message</div>
  <div class="submit abs">SUBMIT</div>
</section>

<footer>
  <div class="footer-band abs"></div>
  <div class="footer-address abs">
    <svg width="11" height="14" viewBox="0 0 11 14" style="vertical-align:-1px"><path d="M5.5 0A5.5 5.5 0 0 0 0 5.5C0 9 5.5 14 5.5 14S11 9 11 5.5A5.5 5.5 0 0 0 5.5 0zm0 7.5a2 2 0 1 1 0-4 2 2 0 0 1 0 4z" fill="#fff"/></svg>
    Lumo IT FZ-LLC, Harbour Trade Park, Unit 12</div>
  <div class="footer-contacts abs">
    <span><svg width="16" height="16" viewBox="0 0 16 16"><path d="M3 1l3 3-2 2c1 2 3 4 5 5l2-2 3 3-2 3C7 15 1 9 1 3z" fill="#fff"/></svg> Tel : 555 010 2233</span><span>|</span>
    <span><svg width="16" height="16" viewBox="0 0 16 16"><rect x="1" y="5" width="14" height="9" fill="#fff"/><rect x="4" y="1" width="8" height="4" fill="#fff"/></svg> Fax : 555 010 4477</span><span>|</span>
    <span><svg width="18" height="14" viewBox="0 0 18 14"><rect width="18" height="14" fill="#fff"/><path d="M0 0l9 7 9-7" fill="none" stroke="#7b1070" stroke-width="1.5"/></svg> Email : hello@lumoit.example</span>
  </div>
  <div class="footer-rule abs"></div>
  <div class="footer-nav abs">Home &nbsp;|&nbsp; About Us &nbsp;|&nbsp; Our Team &nbsp;|&nbsp; Products &nbsp;|&nbsp; Services &nbsp;|&nbsp; Contact</div>
  <div class="footer-copy abs">Copyright © 2019 Lumo IT. All rights reserved.</div>
  <span class="social abs" style="left:996px"></span>
  <span class="social abs" style="left:1036px"></span>
</footer>

</body>
</html>
```